Kestrel Facilities Business Card Design

We would now like to design business cards with the new Kestrel Facilities logo

Target Market(s)

Professional

Industry/Entity Type

Professional services

Contact Information for Business Card

Employee name, title, phone number, email address, corporate office address and logo.

Font styles to use
Sans Serif

Colors
0054AA
0677BA
7BADD7
CADEEF
E8F1F8

Requirements
Must have
• My logo
Should not have
• any other pictures or images besides my logo

```html
<!DOCTYPE html>
<html lang="en">
<head>
<meta charset="utf-8">
<title>Kestrel Facilities – Business Card</title>
<link href="https://fonts.googleapis.com/css2?family=Arimo:wght@400;700&display=swap" rel="stylesheet">
<style>
  :root {
    --brand-blue: #0677BA;
    --brand-bright: #0a7fe0;
    --brand-deep: #0054AA;
    --ink: #333333;
    --rule: #3a3a3a;
    --paper: #f7f7f7;
    --backdrop: #e6e6e4;
    --white: #ffffff;
  }
  * { box-sizing: border-box; margin: 0; padding: 0; }
  html, body {
    width: 1200px;
    height: 801px;
    overflow: hidden;
    background: var(--backdrop);
    font-family: "Arimo", Arial, sans-serif;
  }
  .sheet {
    position: relative;
    width: 1200px;
    height: 801px;
    display: flex;
    align-items: center;
    justify-content: center;
    gap: 50px;
  }
  .card {
    position: relative;
    width: 525px;
    height: 300px;
    border-radius: 2px;
    box-shadow: 0 10px 24px rgba(0,0,0,0.18);
  }
  /* Front */
  .card--front {
    background: var(--paper);
    border-bottom: 3px solid var(--brand-blue);
  }
  .card__brand {
    position: absolute;
    top: 52px;
    right: 44px;
    display: flex;
    align-items: center;
    gap: 10px;
  }
  .brand-mark {
    width: 26px;
    height: 26px;
    background: var(--brand-bright);
  }
  .brand-name {
    font-size: 24px;
    font-weight: 700;
    color: var(--brand-bright);
    letter-spacing: 0.5px;
  }
  .card__identity {
    position: absolute;
    left: 40px;
    top: 96px;
  }
  .person-name {
    font-size: 24px;
    font-weight: 700;
    color: var(--brand-bright);
    line-height: 1.1;
  }
  .person-title {
    font-size: 16px;
    color: var(--ink);
    margin-top: 2px;
  }
  .card__rule {
    position: absolute;
    left: 40px;
    right: 40px;
    top: 150px;
    height: 1px;
    background: var(--rule);
  }
  .contact-list {
    position: absolute;
    left: 40px;
    top: 166px;
    list-style: none;
  }
  .contact-list li {
    display: flex;
    align-items: center;
    gap: 10px;
    font-size: 16px;
    color: var(--ink);
    line-height: 26px;
  }
  .contact-icon { width: 14px; height: 14px; flex: none; }
  .card__address {
    position: absolute;
    right: 40px;
    top: 168px;
    text-align: right;
    font-size: 15px;
    line-height: 1.25;
    color: var(--ink);
  }
  /* Back */
  .card--back {
    background: linear-gradient(160deg, var(--brand-bright) 0%, var(--brand-blue) 100%);
    border-bottom: 3px solid var(--brand-deep);
    display: flex;
    align-items: center;
    padding-left: 52px;
  }
  .card--back .brand-mark { background: var(--white); width: 34px; height: 34px; }
  .card--back .brand-name { color: var(--white); font-size: 32px; }
  .card--back .card__brand { position: static; gap: 14px; }
</style>
</head>
<body>
<main class="sheet">
  <section class="card card--front" aria-label="Business card front">
    <div class="card__brand">
      <span class="brand-mark"></span>
      <span class="brand-name">Kestrel Facilities</span>
    </div>
    <div class="card__identity">
      <p class="person-name">Daniel Reyes</p>
      <p class="person-title">Manager</p>
    </div>
    <div class="card__rule"></div>
    <ul class="contact-list">
      <li>
        <svg class="contact-icon" viewBox="0 0 16 16" aria-hidden="true"><path fill="#0a7fe0" d="M3.6 1.5l2.2 2.8-1.3 1.6c.9 2 2.5 3.6 4.6 4.6l1.6-1.3 2.8 2.2-1.4 2.2C7.6 13.3 2.7 8.4 1.4 3z"/></svg>
        <span>312-555-0147</span>
      </li>
      <li>
        <svg class="contact-icon" viewBox="0 0 16 16" aria-hidden="true"><rect x="1" y="3" width="14" height="10" fill="#0a7fe0"/><path d="M1.5 3.5L8 9l6.5-5.5" stroke="#fff" stroke-width="1.3" fill="none"/></svg>
        <span>d.reyes@kestrelfacilities.com</span>
      </li>
      <li>
        <svg class="contact-icon" viewBox="0 0 16 16" aria-hidden="true"><circle cx="8" cy="8" r="7" fill="#0a7fe0"/><path d="M1 8h14M8 1c-3 3-3 11 0 14M8 1c3 3 3 11 0 14" stroke="#fff" stroke-width="1" fill="none"/></svg>
        <span>www.kestrelfacilities.com</span>
      </li>
    </ul>
    <p class="card__address">Your address, city<br>state, ZIP 0000</p>
  </section>

  <section class="card card--back" aria-label="Business card back">
    <div class="card__brand">
      <span class="brand-mark"></span>
      <span class="brand-name">Kestrel Facilities</span>
    </div>
  </section>
</main>
</body>
</html>
```